Mortgage and Asset Finance Broker Needs a Wordpress Website Design

I need a modern looking Wordpress website to showcase my service as a mortgage and asset broker. I have a company and we work with various lenders to arrange mortgages, as well as commercial lending and business asset finance. The website needs to look professional, be easy to navigate and capture leads. SEO is obviously very important to me. It really needs to be something that shows trust and professioanlism.
Updates

On the home page I will need to have some boxes for Home Loans, Refinancing, Business (and Agriculture) Loans etc. I'd like a carousel in the middle which shows our lenders (so that can have the banks logos added).

It needs to be easy top navigate and showcase all we do - Home Loans, Refinancing, Commercial Loans, Car Loans, Asset Finance etc.

There are plenty of companies on the internet that do this.

There is some good information here https://lendplatehq.com.au/mortgage-broker-homepage/

I need to make sure that editing the website is easy (I think Wordpress has something that allows that).

Also we are very much an Australian business so that is something to advertise.

Industry/Entity Type

Mortgage and Finance Broker

Coding

Coded - Design and coding required

Number of Pages Required

5+ page

Requirements
Must have
• Easy to navigate professional feel. Must be responsive and mobile friendly.
Nice to have
• Homepage with links to inner pages. Contact buttons.

```html
<!DOCTYPE html>
<html lang="en">
<head>
<meta charset="utf-8">
<title>Vantora Financial Services</title>
<link href="https://fonts.googleapis.com/css2?family=Lora:wght@500;600;700&family=Montserrat:wght@400;500;600&display=swap" rel="stylesheet">
<style>
:root{
  --blue:#1f4f9f;
  --orange:#f07c1f;
  --purple:#5a2b86;
  --pink:#d4145a;
  --ink:#111;
  --text:#333;
  --grey:#ececec;
  --night:#0b0b12;
}
*{box-sizing:border-box;margin:0;padding:0}
html,body{width:1200px;height:4326px;overflow:hidden;background:#fff}
body{font-family:"Montserrat",sans-serif;color:var(--text);position:relative}
.abs{position:absolute}
.btn{position:absolute;background:var(--orange);color:#fff;border-radius:30px;font-family:"Lora",serif;font-weight:600;display:flex;align-items:center;justify-content:center}

/* header */
.brand{left:75px;top:30px;font-family:"Lora",serif;font-weight:700;color:var(--blue);font-size:40px;line-height:1;display:flex;align-items:center;gap:10px}
.brand .dot{width:22px;height:22px;background:var(--orange);border-radius:50%}
.brand small{display:block;font-size:13px;letter-spacing:1px;color:var(--ink);font-family:"Montserrat",sans-serif;font-weight:600}
.phone{right:76px;top:14px;display:flex;align-items:center;gap:12px;font-family:"Lora",serif;font-weight:600;font-size:26px;color:var(--blue)}
.phone .ic{width:40px;height:40px;border-radius:50%;background:var(--blue);display:flex;align-items:center;justify-content:center}
.login{left:940px;top:59px;width:155px;height:48px;font-size:15px;letter-spacing:.5px}
.nav{left:0;top:122px;width:1200px;height:58px;background:var(--blue);display:flex;align-items:center;padding-left:80px;gap:37px}
.nav a{color:#fff;text-decoration:none;font-family:"Lora",serif;font-size:16px;letter-spacing:.3px}
.nav a.on{color:var(--orange);text-decoration:underline}

/* hero */
.hero{left:0;top:180px;width:1200px;height:640px;background:linear-gradient(180deg,#4b5a66 0%,#6c7c84 40%,#2e4a4e 70%,#1f3336 100%)}
.hero-title{left:0;width:1200px;text-align:center;color:#fff;font-family:"Lora",serif;font-weight:700}
.arrow{position:absolute}
.hero-wave{left:0;top:700px;width:1200px;height:130px}

.card{position:absolute;background:#fff;border:2px solid #ddd;border-radius:8px;text-align:center}
.card.active{border:3px solid var(--orange)}
.svc{top:688px;width:242px;height:330px}
.svc .ph{position:absolute;left:9px;top:10px;right:9px;height:164px;border-radius:4px}
.svc h3{position:absolute;top:194px;width:100%;font-family:"Lora",serif;color:var(--blue);font-size:22px;font-weight:600}
.svc p{position:absolute;top:228px;left:20px;right:20px;font-size:13px;line-height:22px;color:#444}
.svc .btn{left:50%;transform:translateX(-50%);top:310px;width:143px;height:36px;font-size:13px}

/* lenders */
.lenders{left:0;top:1115px;width:1200px;height:250px;background:var(--grey)}
.sec-title{position:absolute;width:1200px;left:0;text-align:center;font-family:"Lora",serif;font-weight:700;color:var(--ink)}
.lender{position:absolute;top:1232px;height:82px;border-radius:6px;background:#cfcfcf}

/* about */
.about-h{left:705px;top:1462px;font-family:"Lora",serif;font-weight:700;font-size:37px;line-height:42px;color:var(--ink)}
.about-h span{color:var(--blue)}
.about-p{left:705px;width:420px;font-size:13px;line-height:25px;color:#333}

/* team */
.team-band{left:0;top:2015px;width:1200px;height:318px;background:linear-gradient(90deg,#1f4f9f,#5a2b86)}
.member{top:2146px;width:328px;height:366px;box-shadow:0 4px 14px rgba(0,0,0,.08)}
.member .av{position:absolute;left:94px;top:30px;width:140px;height:140px;border-radius:50%;border:2px solid #444}
.member h4{position:absolute;top:186px;width:100%;font-family:"Lora",serif;color:var(--blue);font-size:18px;font-weight:700}
.member .role{position:absolute;top:214px;width:100%;color:var(--orange);font-size:14px}
.member p{position:absolute;top:240px;left:40px;right:40px;font-size:13.5px;line-height:23px}
.member .soc{position:absolute;top:310px;left:0;width:100%;display:flex;justify-content:center;gap:20px}
.soc i{display:block;width:20px;height:20px;border-radius:50%;background:#111}

/* blog */
.blog-bg{left:0;top:2620px;width:1200px;height:805px}
.post{top:2832px;width:328px;height:443px;border:none;border-radius:4px;box-shadow:0 4px 14px rgba(0,0,0,.06)}
.post .ph{position:absolute;left:0;top:0;width:100%;height:202px;border-radius:4px 4px 0 0}
.post .date{position:absolute;top:228px;width:100%;color:var(--pink);font-family:"Lora",serif;font-size:13px;font-weight:600}
.post h4{position:absolute;top:250px;left:20px;right:20px;font-family:"Lora",serif;color:var(--blue);font-size:18.5px;line-height:25px;font-weight:600}
.post p{position:absolute;top:310px;left:12px;right:12px;font-size:13px;line-height:22px}
.post .btn{left:50%;transform:translateX(-50%);top:384px;width:143px;height:36px;font-size:13px}

/* testimonials */
.t-title{left:75px;top:3500px;font-family:"Lora",serif;font-weight:700;font-size:40px;color:var(--ink)}
.t-title span{color:var(--blue)}
.quote{top:3580px;width:516px;height:188px;border:2px solid #d6d6d6;border-radius:6px;box-shadow:0 3px 8px rgba(0,0,0,.06)}
.quote p{position:absolute;left:20px;right:30px;top:22px;font-size:13px;line-height:25px}
.quote .av{position:absolute;left:22px;top:108px;width:70px;height:70px;border-radius:50%;background:var(--orange)}
.quote h5{position:absolute;left:112px;top:116px;font-family:"Lora",serif;color:var(--blue);font-size:21px;font-weight:600}
.quote small{position:absolute;left:112px;top:146px;font-size:13px;color:#111}

/* footer */
.footer{left:0;top:3840px;width:1200px;height:486px}
.f-col{position:absolute;top:3970px}
.f-col h6{font-family:"Lora",serif;color:var(--blue);font-size:18px;font-weight:500;margin-bottom:18px}
.f-col a{display:block;color:#fff;font-size:13px;text-decoration:none;margin-bottom:22px}
.f-col p{color:#fff;font-size:13px;line-height:22px;margin-bottom:12px}
.copy{left:75px;top:4276px;color:#777;font-size:12px}
.f-soc{left:955px;top:4266px;display:flex;gap:20px;align-items:center}
.f-soc i{display:block;width:20px;height:20px;border-radius:50%;background:#fff}
</style>
</head>
<body>

<!-- header -->
<div class="abs brand"><span class="dot"></span><div>Vantora<small>FINANCIAL SERVICES</small></div></div>
<div class="abs phone"><span class="ic"><svg width="20" height="20" viewBox="0 0 24 24"><path fill="#fff" d="M6.6 10.8a15 15 0 0 0 6.6 6.6l2.2-2.2c.3-.3.7-.4 1-.2 1.1.4 2.3.6 3.6.6.6 0 1 .4 1 1V20c0 .6-.4 1-1 1A17 17 0 0 1 3 4c0-.6.4-1 1-1h3.5c.6 0 1 .4 1 1 0 1.3.2 2.5.6 3.6.1.3 0 .7-.2 1z"/></svg></span>1300 555 019</div>
<div class="btn login">CLIENT LOGIN</div>
<nav class="abs nav">
  <a class="on">HOME LOANS</a><a>REFINANCING</a><a>COMMERCIAL LOANS</a><a>CAR LOANS</a><a>ASSET FINANCE</a><a>ABOUT US</a><a>CONTACT US</a>
</nav>

<!-- hero -->
<div class="abs hero" role="img" aria-label="City harbour skyline at sunset"></div>
<div class="abs hero-title" style="top:285px;font-size:118px;line-height:1">VANTORA</div>
<div class="abs hero-title" style="top:400px;font-size:60px;line-height:70px;letter-spacing:2px">FINANCIAL SERVICES</div>
<div class="abs hero-title" style="top:478px;font-family:Montserrat,sans-serif;font-weight:400;font-size:20px;line-height:29px">Nemo enim ipsam voluptatem quia voluptas sit aspe<br>rnatur aut odit aut fugit, sed quia.</div>
<div class="btn" style="left:520px;top:554px;width:158px;height:54px;font-size:16px">Learn More</div>
<svg class="arrow" style="left:72px;top:425px" width="22" height="40"><path d="M18 4 4 20l14 16" stroke="#fff" stroke-width="3" fill="none"/></svg>
<svg class="arrow" style="left:1106px;top:425px" width="22" height="40"><path d="M4 4l14 16L4 36" stroke="#fff" stroke-width="3" fill="none"/></svg>
<svg class="abs hero-wave" viewBox="0 0 1200 130" preserveAspectRatio="none"><path d="M0 110C300 70 500 100 720 90S1050 40 1200 0V130H0Z" fill="#fff"/></svg>

<!-- service cards -->
<div class="card svc" style="left:75px"><div class="ph" role="img" aria-label="Handshake over a model house" style="background:linear-gradient(135deg,#cfd3d6,#8d9399)"></div><h3>Home Loans</h3><p>Duis aute irure dolor in reprehenderit in voluptate velit esse cillum.</p><div class="btn">Find Out More</div></div>
<div class="card svc active" style="left:344px"><div class="ph" role="img" aria-label="Hands using a calculator" style="background:linear-gradient(135deg,#b9a58e,#5a524a)"></div><h3>Refinancing</h3><p>Duis aute irure dolor in reprehenderit in voluptate velit esse cillum.</p><div class="btn">Find Out More</div></div>
<div class="card svc" style="left:616px"><div class="ph" role="img" aria-label="Business paperwork with calculator" style="background:linear-gradient(135deg,#e3e0dc,#8c8a88)"></div><h3>Business Loans</h3><p>Duis aute irure dolor in reprehenderit in voluptate velit esse cillum.</p><div class="btn">Find Out More</div></div>
<div class="card svc" style="left:885px"><div class="ph" role="img" aria-label="Sack of grain over farmland" style="background:linear-gradient(180deg,#e9a45a,#6b4a2c)"></div><h3>Agriculture Loans</h3><p>Duis aute irure dolor in reprehenderit in voluptate velit esse cillum.</p><div class="btn">Find Out More</div></div>

<!-- lenders -->
<div class="abs lenders"></div>
<div class="sec-title" style="top:1160px;font-size:32px">Our Lenders</div>
<div class="lender" style="left:75px;width:274px;background:#fff;border:1px solid #ccc"></div>
<div class="lender" style="left:392px;width:120px;border-radius:50%"></div>
<div class="lender" style="left:560px;width:262px;height:30px;top:1258px"></div>
<div class="lender" style="left:882px;width:84px;height:62px;top:1240px"></div>
<div class="lender" style="left:1022px;width:106px;height:60px;top:1240px"></div>

<!-- about -->
<svg class="abs" style="left:75px;top:1438px" width="610" height="500">
  <circle cx="245" cy="246" r="248" fill="#d4145a"/>
  <circle cx="242" cy="248" r="242" fill="#a99b86" role="img" aria-label="Advisor with clients around a laptop"/>
  <circle cx="456" cy="308" r="152" fill="#d4145a"/>
  <circle cx="458" cy="310" r="146" fill="#54626d" role="img" aria-label="Model house with coins"/>
</svg>
<div class="abs about-h">ABOUT <span>VANTORA<br>FINANCIAL SERVICES</span></div>
<div class="abs about-p" style="top:1568px">Sed ut perspiciatis unde omnis iste natus error sit voluptatem accusantium doloremque laudantium, totam rem aperiam, eaque ipsa quae ab illo inventore veritatis et quasi architecto beatae vitae dicta sunt explicabo. Nemo enim ipsam voluptatem quia voluptas sit aspernatur aut odit aut fugit, sed quia consequuntur magni dolores eos qui ratione voluptatem sequi nesciunt.</div>
<div class="abs about-p" style="top:1753px">Sed ut perspiciatis unde omnis iste natus error sit voluptatem accusantium doloremque laudantium, totam rem aperiam, eaque ipsa quae ab illo inventore.</div>
<div class="btn" style="left:705px;top:1855px;width:180px;height:55px;font-size:17px">Learn More</div>

<!-- team -->
<div class="abs team-band"></div>
<div class="sec-title" style="top:2062px;font-size:38px;color:#fff;letter-spacing:1px">MEET OUR TEAM</div>
<svg class="arrow" style="left:40px;top:2290px" width="20" height="34"><path d="M16 2 3 17l13 15" stroke="#fff" stroke-width="3" fill="none"/></svg>
<svg class="arrow" style="left:1140px;top:2290px" width="20" height="34"><path d="M4 2l13 15L4 32" stroke="#fff" stroke-width="3" fill="none"/></svg>
<div class="card member" style="left:75px"><div class="av" role="img" aria-label="Portrait of advisor" style="background:linear-gradient(#e8e8e8,#2c3e5c)"></div><h4>Johnathan J.</h4><div class="role">Advisor</div><p>Sed ut perspiciatis unde omnis iste natus error sit voluptatem.</p><div class="soc"><i></i><i></i><i></i></div></div>
<div class="card member active" style="left:437px"><div class="av" role="img" aria-label="Portrait of advisor" style="background:linear-gradient(#dcdcdc,#222)"></div><h4>Johnathan J.</h4><div class="role">Advisor</div><p>Sed ut perspiciatis unde omnis iste natus error sit voluptatem.</p><div class="soc"><i></i><i></i><i></i></div></div>
<div class="card member" style="left:797px"><div class="av" role="img" aria-label="Portrait of advisor" style="background:linear-gradient(#d8dbe0,#2d3a52)"></div><h4>Johnathan J.</h4><div class="role">Advisor</div><p>Sed ut perspiciatis unde omnis iste natus error sit voluptatem.</p><div class="soc"><i></i><i></i><i></i></div></div>

<!-- blog -->
<svg class="abs blog-bg" viewBox="0 0 1200 805" preserveAspectRatio="none"><path d="M0 20C300 -10 600 60 900 20S1150 0 1200 10V780C900 740 700 800 400 790S100 770 0 790Z" fill="var(--grey)"/></svg>
<div class="sec-title" style="top:2743px;font-size:40px">LATEST <span style="color:var(--blue)">BLOG</span></div>
<svg class="arrow" style="left:40px;top:3037px" width="20" height="34"><path d="M16 2 3 17l13 15" stroke="#555" stroke-width="2.5" fill="none"/></svg>
<svg class="arrow" style="left:1140px;top:3037px" width="20" height="34"><path d="M4 2l13 15L4 32" stroke="var(--pink)" stroke-width="3" fill="none"/></svg>
<div class="card post" style="left:75px"><div class="ph" role="img" aria-label="Advisor shaking hands with couple" style="background:linear-gradient(135deg,#d9cfc3,#6e5d4f)"></div><div class="date">Mar16, 2025</div><h4>Excepteur sint occaecat cupid atat non proident</h4><p>Duis aute irure dolor in reprehenderit in voluptate velit esse cillum dolore eu fugiat nulla pariatur enim ipsam volup.</p><div class="btn">Find Out More</div></div>
<div class="card post" style="left:437px"><div class="ph" role="img" aria-label="Advisor meeting senior couple" style="background:linear-gradient(135deg,#e4ddd2,#7a6a5a)"></div><div class="date">Mar16, 2025</div><h4>Excepteur sint occaecat cupid atat non proident</h4><p>Duis aute irure dolor in reprehenderit in voluptate velit esse cillum dolore eu fugiat nulla pariatur enim ipsam volup.</p><div class="btn">Find Out More</div></div>
<div class="card post" style="left:797px"><div class="ph" role="img" aria-label="Signing loan papers with calculator" style="background:linear-gradient(135deg,#c9c9c9,#4a4a4a)"></div><div class="date">Mar16, 2025</div><h4>Excepteur sint occaecat cupid atat non proident</h4><p>Duis aute irure dolor in reprehenderit in voluptate velit esse cillum dolore eu fugiat nulla pariatur enim ipsam volup.</p><div class="btn">Find Out More</div></div>

<!-- testimonials -->
<div class="abs t-title">WHAT OUR <span>CUSTOMER SAYS</span></div>
<svg class="arrow" style="left:1062px;top:3513px" width="18" height="30"><path d="M14 2 3 15l11 13" stroke="#111" stroke-width="2.5" fill="none"/></svg>
<svg class="arrow" style="left:1112px;top:3513px" width="18" height="30"><path d="M4 2l11 13L4 28" stroke="var(--purple)" stroke-width="2.5" fill="none"/></svg>
<div class="card quote" style="left:72px"><p>“ Sed ut perspiciatis unde omnis iste natus error sit voluptatem accusantium doloremque laudantium, totam rem aperiam, eaque ipsa quae ab illo inventoreuis aute irure dolor..”</p><div class="av"></div><h5>Name Heading</h5><small>Location</small></div>
<div class="card quote" style="left:618px"><p>“ Sed ut perspiciatis unde omnis iste natus error sit voluptatem accusantium doloremque laudantium, totam rem aperiam, eaque ipsa quae ab illo inventoreuis aute irure dolor..”</p><div class="av"></div><h5>Name Heading</h5><small>Location</small></div>

<!-- footer -->
<svg class="abs footer" viewBox="0 0 1200 486" preserveAspectRatio="none"><path d="M0 50C250 0 450 70 700 40S1050 0 1200 20V486H0Z" fill="var(--night)"/></svg>
<div class="abs brand" style="top:3975px"><span class="dot"></span><div style="color:#fff">Vantora<small style="color:#fff">FINANCIAL SERVICES</small></div></div>
<p class="abs" style="left:75px;top:4083px;width:285px;color:#fff;font-size:13px;line-height:23px">Nemo enim ipsam voluptatem quia voluptas sit aspernatur aut odit aut fugit, sed quia consequuntur magni</p>
<div class="f-col" style="left:411px"><h6>Quick Links</h6><a>Home Loans</a><a>Refinancing</a><a>Commercial Loans</a><a>Car Loans</a><a>Asset Finance</a></div>
<div class="f-col" style="left:653px"><h6>Resources</h6><a>Home Loans</a><a>Refinancing</a><a>Commercial Loans</a><a>Car Loans</a><a>Asset Finance</a></div>
<div class="f-col" style="left:885px;width:260px"><h6>Contact Us</h6><p>Excepteur sint occaecat cupidatat non proident</p><p>1300 555 019</p><p>hello@vantorafinance.com.au</p></div>
<div class="abs" style="left:0;top:4250px;width:1200px;height:1px;background:#2a2a33"></div>
<div class="abs copy">© Copyright 2025 Company Name All Rights Reserved.</div>
<div class="abs f-soc"><i></i><i style="background:var(--orange)"></i><i></i><i></i><i></i></div>

</body>
</html>
```